Business Cards + Flyer + Letterhead for Care Recruitment Agency

We are a recruitment agency for the health & care sector. We need designs made for business cards, A5 double-sided flyer, and a letterhead template.

Our branding message is professionalism, care, compassion, expertise. We are experts in recruitment for the care & health industry.

Our logo source files and colours are here - https://www.filevault-example.net/sh/q8rn27lpzw4xkc/BBRtLm3QPW92dKfYhNvZceLmo?dl=0

For the business card, I have attached an example we like. We want a vertical business card design, something very similar to the example given. The design should match our logo in terms of brand colors. On one side should be our logo, our website (www.holbrookelune.co.uk) and Care Recruitment Specialists written somewhere visible that fits, between our logo and the website at the bottom. On the other side should be our details.

Details on the front:

Logo with slogan
Care Recruitment Specialists
www.holbrookelune.co.uk

Details on the back:

Dominic Argyros
Managing Director

Radley Court, 40-48 Pellow St, Birmingham, B7 9QX
07612 495137
dominic@holbrookelune.co.uk
www.holbrookelune.co.uk

Nadia Holbrooke
Business Development Director

07731 284956
nadia@holbrookelune.co.uk
www.holbrookelune.co.uk

For the A5 flyer, I have attached some pictures we've used for the website, which could be used for the flyer as well. To get a better idea of our branding, please visit our website - https://holbrookelune.co.uk/

The text for the flyer is also attached.

Finally, the letterhead template should be a docx template with our logo and our identifiable branding (the same shapes and matching colours you will come up with for the business cards and flyer).

```html
<!DOCTYPE html>
<html lang="en">
<head>
<meta charset="utf-8">
<title>Holbrooke Lune – Stationery</title>
<link rel="stylesheet" href="https://fonts.googleapis.com/css2?family=Didact+Gothic&family=Lato:wght@300;400;700&display=swap">
<style>
  :root {
    --blue-deep: #0a7cc4;
    --blue-mid: #1590d4;
    --blue-light: #2eaae2;
    --navy: #1d4f91;
    --ink: #5b5f66;
    --muted: #b9bcc2;
    --paper: #ffffff;
    --stage: #eeeff1;
  }
  * { box-sizing: border-box; margin: 0; padding: 0; }
  html, body { width: 1200px; height: 1200px; overflow: hidden; }
  body {
    background: var(--stage);
    font-family: "Lato", sans-serif;
    position: relative;
  }
  .sheet, .card {
    position: absolute;
    background: var(--paper);
    overflow: hidden;
    box-shadow: 0 6px 18px rgba(0,0,0,0.12);
  }
  .shape-layer { position: absolute; inset: 0; width: 100%; height: 100%; }

  /* Brand lockup: name set in the text font, one colour, one weight */
  .brand { position: absolute; display: flex; align-items: center; gap: 10px; }
  .brand__dot { border-radius: 50%; background: var(--blue-light); flex: none; }
  .brand__name {
    font-family: "Lato", sans-serif; font-weight: 700;
    color: var(--navy); letter-spacing: 2px; line-height: 1; white-space: nowrap;
  }

  /* Letterhead */
  .letterhead { left: 66px; top: 170px; width: 573px; height: 764px; }
  .letterhead__header {
    position: absolute; left: 0; top: 0; width: 100%; height: 255px;
    background: linear-gradient(180deg, #ffffff 20%, #eef0f2 100%);
  }
  .letterhead .brand { left: 57px; top: 106px; }
  .letterhead .brand__dot { width: 46px; height: 46px; }
  .letterhead .brand__name { font-size: 20px; }

  .sender { position: absolute; right: 77px; top: 275px; text-align: right; }
  .sender__name { font-size: 12px; font-weight: 700; color: var(--navy); }
  .sender__line { font-size: 9.5px; color: var(--ink); margin-top: 8px; }
  .sender__line + .sender__line { margin-top: 4px; }
  .sender__line b { color: var(--navy); }

  .salutation { position: absolute; left: 57px; top: 296px; font-size: 12px; font-weight: 700; color: var(--navy); line-height: 17px; }
  .letter-body {
    position: absolute; left: 57px; top: 346px; width: 439px;
    font-family: "Didact Gothic", sans-serif; font-size: 11.2px; line-height: 15.4px;
    color: var(--ink); text-align: justify; letter-spacing: 0.2px;
  }
  .letter-body p + p { margin-top: 15px; }
  .signature { position: absolute; left: 340px; top: 556px; width: 156px; height: 46px; background: #eceef1; border-radius: 3px; }
  .signature-name { position: absolute; right: 77px; top: 604px; font-size: 8px; color: var(--muted); letter-spacing: 0.3px; }

  .letter-footer { position: absolute; right: 27px; top: 697px; text-align: right; color: #fff; font-size: 9.5px; line-height: 14px; }
  .letter-footer__phones { margin-top: 6px; }
  .letter-footer__phones span + span { margin-left: 18px; }

  /* Cards */
  .card { left: 781px; width: 351px; height: 199px; }
  .card--front { top: 197px; }
  .card--dominic { top: 416px; }
  .card--nadia { top: 626px; }
  .card--front .brand { left: 0; right: 0; top: 48px; justify-content: center; }
  .card--front .brand__dot { width: 32px; height: 32px; }
  .card--front .brand__name { font-size: 17px; }
  .card__specialism {
    position: absolute; left: 0; right: 0; top: 111px; text-align: center;
    font-size: 9.5px; letter-spacing: 2.6px; color: var(--navy); font-weight: 400;
  }
  .person { position: absolute; left: 8px; width: 160px; top: 86px; text-align: center; }
  .person__name { font-size: 15px; font-weight: 300; color: var(--ink); letter-spacing: 0.3px; white-space: nowrap; }
  .person__name b { font-weight: 700; color: #3d4046; }
  .person__role { font-size: 7.2px; color: #3d4046; margin-top: 3px; }
  .card__divider { position: absolute; left: 169px; top: 47px; width: 1px; height: 124px; background: #dfe2e6; }
  .contact-list { position: absolute; left: 186px; top: 52px; list-style: none; }
  .contact-list li { display: flex; align-items: center; height: 20px; margin-bottom: 10px; font-size: 7.2px; color: #2b2e33; line-height: 9px; }
  .contact-list li.tall { height: 22px; margin-bottom: 8px; }
  .contact-list svg { width: 20px; height: 20px; flex: none; margin-right: 6px; }
</style>
</head>
<body>

<!-- Letterhead -->
<section class="sheet letterhead">
  <div class="letterhead__header"></div>
  <svg class="shape-layer" viewBox="0 0 573 764" preserveAspectRatio="none" aria-hidden="true">
    <path d="M0,0 H251 C170,28 80,75 0,115 Z" fill="var(--blue-light)"/>
    <path d="M0,0 H174 C110,22 50,50 0,73 Z" fill="var(--blue-deep)"/>
    <path d="M446,0 H573 V39 C530,20 490,8 446,0 Z" fill="var(--blue-light)"/>
    <path d="M0,656 C110,722 320,748 573,598 V764 H0 Z" fill="var(--blue-light)"/>
    <path d="M0,690 C140,748 380,752 573,612 V764 H0 Z" fill="var(--blue-mid)"/>
    <path d="M0,720 C160,764 400,740 573,650 V764 H0 Z" fill="var(--blue-deep)"/>
  </svg>

  <div class="brand">
    <span class="brand__dot"></span>
    <span class="brand__name">HOLBROOKE LUNE</span>
  </div>

  <div class="sender">
    <div class="sender__name">MR. Dominic Argyros</div>
    <div class="sender__line"><b>M.</b> 0121 7612 495137</div>
    <div class="sender__line"><b>E.</b> dominic@holbrookelune.co.uk</div>
  </div>

  <div class="salutation">Monday, November 24, 2020<br>Dear Campany Team,</div>

  <div class="letter-body">
    <p>Lorem ipsum dolor sit amet, consectetur adipiscing elit. Fusce dignissim pretium consectetur. Curabitur tempor posuere massa in varius. Pellentesque viverra nibh eu vehicula mattis. Nullam porta facilisis justo, a feugiat dolor sodales sed. Vestibulum neque nisi, elementum tincidunt metus sit amet, egestas bibendum enim. Aenean a blandit elit, vel rutrum mi. Nunc dapibus turpis sed massa aliquet tincidunt.</p>
    <p>Pellentesque id neque ligula. Nullam posuere, ligula a mattis posuere, lacus nisl congue ornare diam.</p>
    <p>Pellentesque vel nibh tempus, ullamcorper tortor sed, bibendum augue. Phasellus sollicitudin justo et quam aliquam sollicitudin. Sed eget nibh mollis, mattis sem et, viverra nulla.</p>
  </div>

  <div class="signature" role="img" aria-label="Handwritten signature of the sender"></div>
  <div class="signature-name">MR. DOMINIC ARGYROS</div>

  <div class="letter-footer">
    <div>Radley Court, 40-48 Pellow St,<br>Birmingham, B7 9QX</div>
    <div class="letter-footer__phones"><span>M. 0121 7612 495137</span><span>T. 0121 7612 495137</span></div>
  </div>
</section>

<!-- Business card: front -->
<section class="card card--front">
  <svg class="shape-layer" viewBox="0 0 351 199" preserveAspectRatio="none" aria-hidden="true">
    <path d="M0,116 C60,150 140,166 200,164 C260,162 310,150 351,129 V199 H0 Z" fill="var(--blue-light)"/>
    <path d="M0,142 C80,170 160,186 240,184 C290,182 325,172 351,160 V199 H0 Z" fill="var(--blue-mid)"/>
    <path d="M0,160 C90,190 220,196 351,178 V199 H0 Z" fill="var(--blue-deep)"/>
  </svg>
  <div class="brand">
    <span class="brand__dot"></span>
    <span class="brand__name">HOLBROOKE LUNE</span>
  </div>
  <div class="card__specialism">CARE RECRUITMENT SPECIALISTS</div>
</section>

<!-- Business card: Dominic -->
<section class="card card--dominic">
  <svg class="shape-layer" viewBox="0 0 351 199" preserveAspectRatio="none" aria-hidden="true">
    <path d="M0,127 C70,160 150,178 230,176 C290,174 325,166 351,158 V199 H0 Z" fill="var(--blue-light)"/>
    <path d="M0,145 C90,178 200,190 351,170 V199 H0 Z" fill="var(--blue-mid)"/>
    <path d="M0,168 C100,194 240,196 351,182 V199 H0 Z" fill="var(--blue-deep)"/>
  </svg>
  <div class="person">
    <div class="person__name">DOMINIC <b>ARGYROS</b></div>
    <div class="person__role">MANAGING DIRECTOR</div>
  </div>
  <div class="card__divider"></div>
  <ul class="contact-list">
    <li><svg viewBox="0 0 20 20" aria-hidden="true"><circle cx="10" cy="10" r="10" fill="var(--blue-light)"/><rect x="5" y="6.5" width="10" height="7" rx="1" fill="none" stroke="#fff" stroke-width="1.2"/><path d="M5.3,7 L10,11 L14.7,7" fill="none" stroke="#fff" stroke-width="1.2"/></svg>dominic@holbrookelune.co.uk</li>
    <li><svg viewBox="0 0 20 20" aria-hidden="true"><circle cx="10" cy="10" r="10" fill="var(--blue-light)"/><path d="M7,5 L8.8,5 L9.6,7.8 L8.5,8.8 C9.2,10.4 10,11.2 11.4,11.9 L12.4,10.8 L15,11.6 L15,13.4 C15,14.2 14.3,14.7 13.5,14.6 C9.5,14.1 6,10.6 5.5,6.6 C5.4,5.8 6.1,5 7,5 Z" fill="#fff"/></svg>0121 7612 495137</li>
    <li class="tall"><svg viewBox="0 0 20 20" aria-hidden="true"><circle cx="10" cy="10" r="10" fill="var(--blue-light)"/><path d="M10,4.5 L15.5,9.5 H14 V15 H11.3 V12 H8.7 V15 H6 V9.5 H4.5 Z" fill="#fff"/></svg>Radley Court, 40-48 Pellow St,<br>Birmingham, B7 9QX</li>
    <li><svg viewBox="0 0 20 20" aria-hidden="true"><circle cx="10" cy="10" r="10" fill="var(--blue-light)"/><path d="M7.5,5 L13.5,10.5 L10.6,10.8 L12.2,14.2 L10.9,14.8 L9.3,11.4 L7.5,13.4 Z" fill="#fff"/></svg>www.holbrookelune.co.uk</li>
  </ul>
</section>

<!-- Business card: Nadia -->
<section class="card card--nadia">
  <svg class="shape-layer" viewBox="0 0 351 199" preserveAspectRatio="none" aria-hidden="true">
    <path d="M0,127 C70,160 150,178 230,176 C290,174 325,166 351,158 V199 H0 Z" fill="var(--blue-light)"/>
    <path d="M0,145 C90,178 200,190 351,170 V199 H0 Z" fill="var(--blue-mid)"/>
    <path d="M0,168 C100,194 240,196 351,182 V199 H0 Z" fill="var(--blue-deep)"/>
  </svg>
  <div class="person">
    <div class="person__name">NADIA <b>HOLBROOKE</b></div>
    <div class="person__role">BUSINESS DEVELOPMENT DIRECTOR</div>
  </div>
  <div class="card__divider"></div>
  <ul class="contact-list">
    <li><svg viewBox="0 0 20 20" aria-hidden="true"><circle cx="10" cy="10" r="10" fill="var(--blue-light)"/><rect x="5" y="6.5" width="10" height="7" rx="1" fill="none" stroke="#fff" stroke-width="1.2"/><path d="M5.3,7 L10,11 L14.7,7" fill="none" stroke="#fff" stroke-width="1.2"/></svg>nadia@holbrookelune.co.uk</li>
    <li><svg viewBox="0 0 20 20" aria-hidden="true"><circle cx="10" cy="10" r="10" fill="var(--blue-light)"/><path d="M7,5 L8.8,5 L9.6,7.8 L8.5,8.8 C9.2,10.4 10,11.2 11.4,11.9 L12.4,10.8 L15,11.6 L15,13.4 C15,14.2 14.3,14.7 13.5,14.6 C9.5,14.1 6,10.6 5.5,6.6 C5.4,5.8 6.1,5 7,5 Z" fill="#fff"/></svg>0121 07731 284956</li>
    <li class="tall"><svg viewBox="0 0 20 20" aria-hidden="true"><circle cx="10" cy="10" r="10" fill="var(--blue-light)"/><path d="M10,4.5 L15.5,9.5 H14 V15 H11.3 V12 H8.7 V15 H6 V9.5 H4.5 Z" fill="#fff"/></svg>Radley Court, 40-48 Pellow St,<br>Birmingham, B7 9QX</li>
    <li><svg viewBox="0 0 20 20" aria-hidden="true"><circle cx="10" cy="10" r="10" fill="var(--blue-light)"/><path d="M7.5,5 L13.5,10.5 L10.6,10.8 L12.2,14.2 L10.9,14.8 L9.3,11.4 L7.5,13.4 Z" fill="#fff"/></svg>www.holbrookelune.co.uk</li>
  </ul>
</section>

</body>
</html>
```